Harborline Lending and Capital. We provide MOSTLY residential home mortgages in Florida AND commercial loans for investment properties throughout the United states.
I would love to emulate so of the lender sites that are available on the internet but I would like to have the site as popular as possible for SEO purposes. Clients can already click the link to take them to the mortgage application where they can complete that and upload documents. If you could polish that up for me that would be great. I can also provide you with great detail on loan programs that are currently being offered. WE OFFER ALL MORTGAGE LENDING PRODUCTS. I would also like to add something in reference to the rate but I don't think it's legal to actually state or promise a rate for mortgage since they vary based on loan type, client and other criteria...

On the Harborline real estate site I would like to add a link or some way for clients to be able to put in credit card information to render services ...

Please let me know what you need from me

Thank you !!

Current link to site to improve and code

https://harborlinelendingandcapital.example/

Industry/Entity Type

Residential and commmercial lending

Coding

Coded - Design and coding required

Number of Pages Required

2 page

Requirements
Must have
• Love to integrate Mortgage interest rates even if general
Nice to have
• Link to fill out mortgage application via Quorvel LPX software

```html
<!DOCTYPE html>
<html lang="en">
<head>
<meta charset="utf-8">
<title>Harborline Lending and Capital</title>
<link href="https://fonts.googleapis.com/css2?family=Montserrat:wght@300;400;500;600;700&display=swap" rel="stylesheet">
<style>
:root{
  --green-dark:#1f3b1c;
  --green-deep:#2c4a2a;
  --lime:#8cbb3c;
  --lime-soft:#9cc54e;
  --ink:#1d1d1d;
  --muted:#9a9a9a;
  --panel:#e9ebe7;
  --row:#f2f2f2;
  --white:#ffffff;
}
*{margin:0;padding:0;box-sizing:border-box}
html,body{width:1200px;height:3849px;overflow:hidden;background:var(--white)}
body{font-family:"Montserrat",sans-serif;color:var(--ink);position:relative}
.abs{position:absolute}
.topline{left:0;top:0;width:1200px;height:8px;background:var(--lime)}

/* header */
.brand-tab{left:96px;top:8px;width:387px;height:127px;background:var(--white);border-radius:0 0 14px 14px;z-index:3;display:flex;align-items:center;gap:14px;padding-left:18px}
.brand-dot{width:60px;height:60px;border-radius:50%;background:var(--green-dark);flex:none}
.brand-name{font-size:8.5px;font-weight:700;color:var(--green-dark);letter-spacing:.3px;line-height:1.7;white-space:nowrap}
.nav{top:48px;font-size:17px;color:#333}
.nav.active{color:var(--lime)}
.callback{left:907px;top:42px;width:181px;height:40px;background:var(--lime);color:#fff;border-radius:6px;font-size:14px;font-weight:600;display:flex;align-items:center;justify-content:center}

/* hero */
.hero{left:0;top:115px;width:1200px;height:514px;background:linear-gradient(90deg,var(--green-dark) 0%,#2f4b2c 38%,#7d8a78 62%,#b7b2a2 85%,#8a8272 100%)}
.hero-kicker{left:112px;top:250px;font-size:19px;color:#fff;line-height:28px;font-weight:500}
.hero-title{left:112px;top:320px;font-size:26px;color:#fff;font-weight:600;line-height:36px}
.hero-title span{color:var(--lime)}
.hero-btn{left:112px;top:412px;width:545px;height:50px;background:var(--lime);border-radius:6px;color:#fff;font-size:17px;font-weight:600;display:flex;align-items:center;justify-content:center}
.hero-arrow{top:353px;width:38px;height:38px;border-radius:50%;background:#111;display:flex;align-items:center;justify-content:center}

/* section headings */
.mark{width:30px;height:30px;border-radius:50%;background:var(--green-dark);left:585px}
.kicker{left:0;width:1200px;text-align:center;color:var(--lime);font-size:16px}
.title{left:0;width:1200px;text-align:center;font-size:39px;font-weight:500;letter-spacing:.5px}
.lead{left:195px;width:810px;text-align:center;color:var(--muted);font-size:16px;line-height:25px;font-weight:300}

/* loan cards */
.card{top:976px;width:259px;height:249px;background:#fff;box-shadow:0 4px 18px rgba(0,0,0,.09);border-bottom:7px solid var(--green-dark)}
.card-icon{position:absolute;left:25px;top:-37px;width:74px;height:74px;border-radius:50%;background:#fff;box-shadow:0 3px 12px rgba(0,0,0,.1);display:flex;align-items:center;justify-content:center}
.card h3{position:absolute;left:26px;top:68px;font-size:17px;font-weight:500;line-height:25px}
.card p{position:absolute;left:26px;top:134px;width:190px;font-size:15px;color:var(--muted);line-height:22.5px;font-weight:300}

/* about */
.about{left:0;top:1313px;width:1200px;height:502px;background:var(--panel)}
.about-photo{left:0;top:0;width:1200px;height:502px}
.about-title{left:112px;top:1452px;font-size:36px;font-weight:500;line-height:46px;white-space:nowrap}
.about-text{left:112px;top:1561px;width:430px;font-size:15.5px;color:var(--muted);line-height:25px;font-weight:300}
.btn{background:var(--lime);color:#fff;border-radius:6px;font-weight:600;display:flex;align-items:center;justify-content:center}

/* properties */
.prop{top:2113px;height:334px}
.prop-label{position:absolute;left:24px;bottom:30px;color:#fff;font-size:19px;font-weight:500}
.prop-active{left:272px;top:2068px;width:351px;height:412px;background:linear-gradient(180deg,#9cc54e,#8bb843);border-bottom:8px solid var(--green-dark)}
.prop-bar{left:9px;top:2447px;width:1179px;height:6px;background:var(--lime)}

/* lending */
.gauge-tag{width:40px;height:22px;background:var(--green-dark);color:#fff;font-size:10px;border-radius:3px;display:flex;align-items:center;justify-content:center}
.calc{left:662px;top:2757px;width:424px;height:300px;border-radius:8px;overflow:hidden;box-shadow:0 3px 14px rgba(0,0,0,.08)}
.calc-head{height:64px;background:var(--green-dark);color:#fff;font-size:17px;font-weight:500;display:flex;align-items:center;padding-left:27px}
.calc-row{height:56px;display:flex;justify-content:space-between;align-items:center;padding:0 30px;font-size:17px;font-weight:500}
.calc-total{background:var(--lime-soft)!important;color:var(--green-dark);height:68px;font-size:16px;line-height:19px}

/* contact */
.contact{left:0;top:3167px;width:1200px;height:490px;background:linear-gradient(90deg,#213c1f,#2c4a2a 60%,#25421f)}
.contact-title{left:154px;top:3253px;font-size:38px;color:#fff;font-weight:600}
.info-icon{left:154px;width:45px;height:45px;background:#fff;border-radius:4px;display:flex;align-items:center;justify-content:center}
.info-label{left:212px;color:#fff;font-size:19px;font-weight:600}
.info-value{left:212px;color:#fff;font-size:15px}
.field{left:612px;width:411px;height:45px;background:#fff;border-radius:3px;font-size:13px;color:#333;padding:15px 16px}

/* footer */
.foot-nav{top:3712px;font-size:16px;color:#222}
.social{top:3745px;width:13px;height:13px;background:var(--green-dark);border-radius:2px}
</style>
</head>
<body>
<div class="abs topline"></div>

<header>
  <div class="abs brand-tab"><span class="brand-dot"></span><span class="brand-name">HARBORLINE LENDING AND CAPITAL OF FLORIDA<br>BUSINESS AND COMMERCIAL DIVISION</span></div>
  <div class="abs nav active" style="left:539px">Home</div>
  <div class="abs nav" style="left:654px">About</div>
  <div class="abs nav" style="left:769px">Properties</div>
  <div class="abs callback">Request a Callback</div>
</header>

<section>
  <div class="abs hero" role="img" aria-label="Row of two-storey suburban homes under a green overlay"></div>
  <div class="abs hero-kicker">RESIDENTIAL HOME LOANS IN FLORIDA AND<br>COMMERCIAL LENDING IN AMERICA</div>
  <div class="abs hero-title">YOUR BEST RESOURCE <span>FOR HASSLE-FREE,</span><br>LOW COST MORTGAGE ORIGINATION</div>
  <div class="abs hero-btn">FILL OUT MORTGAGE APPLICATION TO BEGIN LENDING PR</div>
  <div class="abs hero-arrow" style="left:34px"><svg width="12" height="16" viewBox="0 0 12 16"><path d="M8 2 2 8l6 6" stroke="#fff" stroke-width="2" fill="none"/></svg></div>
  <div class="abs hero-arrow" style="left:1098px"><svg width="12" height="16" viewBox="0 0 12 16"><path d="M4 2l6 6-6 6" stroke="#fff" stroke-width="2" fill="none"/></svg></div>
</section>

<section>
  <div class="abs mark" style="top:722px"></div>
  <div class="abs kicker" style="top:772px">WHAT WE DO</div>
  <div class="abs title" style="top:803px">OUR &nbsp;LOAN PROGRAMS</div>
  <div class="abs lead" style="top:859px">Lorem ipsum dolor sit amet, consectetur adipiscing elit, sed do eiusmod tempor incididunt ut labore et dolore magna aliqua. Ut enim ad minim veniam, quis nostrud exercitation ullamco</div>

  <div class="abs card" style="left:179px">
    <div class="card-icon"><svg width="36" height="36" viewBox="0 0 36 36" fill="none" stroke="#333" stroke-width="1.6"><path d="M9 17 18 9l9 8M12 15v9h12v-9"/><path d="M3 22l6 8h6M33 22l-6 8h-6"/></svg></div>
    <h3>Residential Home<br>Mortgages</h3>
    <p>Lorem ipsum dolor sit amet, consectetur adipiscing elit, sed do eiusmod tempor</p>
  </div>
  <div class="abs card" style="left:471px">
    <div class="card-icon"><svg width="36" height="36" viewBox="0 0 36 36" fill="none" stroke="#333" stroke-width="1.6"><ellipse cx="22" cy="9" rx="8" ry="3"/><path d="M14 9v8c0 1.7 3.6 3 8 3s8-1.3 8-3V9"/><path d="M3 24h8l6 3h8M3 31h20l8-6"/></svg></div>
    <h3>Commercial Loans</h3>
    <p>Lorem ipsum dolor sit amet, consectetur adipiscing elit, sed do eiusmod tempor</p>
  </div>
  <div class="abs card" style="left:760px">
    <div class="card-icon"><svg width="36" height="36" viewBox="0 0 36 36" fill="none" stroke="#333" stroke-width="1.6"><path d="M4 32h28M8 32V22M14 32V18M20 32V20M26 32V14"/><path d="M6 16l8-6 6 4 10-9"/></svg></div>
    <h3>Investment Properties</h3>
    <p>Lorem ipsum dolor sit amet, consectetur adipiscing elit, sed do eiusmod tempor</p>
  </div>
</section>

<section>
  <div class="abs about">
    <svg class="abs about-photo" width="1200" height="502" viewBox="0 0 1200 502">
      <defs><linearGradient id="aboutTone" x1="0" y1="0" x2="1" y2="1"><stop offset="0" stop-color="#7fa0c9"/><stop offset=".5" stop-color="#3b3a3c"/><stop offset="1" stop-color="#b9a98d"/></linearGradient></defs>
      <polygon points="690,0 603,218 711,502 675,502 588,218 675,0" fill="#8cbb3c"/>
      <polygon points="703,0 1200,0 1200,502 718,502 616,218" fill="url(#aboutTone)" role="img" aria-label="Modern two-storey house with dark cladding and glass"/>
    </svg>
  </div>
  <div class="abs mark" style="left:115px;top:1374px"></div>
  <div class="abs" style="left:112px;top:1422px;color:var(--lime);font-size:16px">ABOUT</div>
  <div class="abs about-title">HARBORLINE LENDING<br>AND CAPITAL</div>
  <div class="abs about-text">Harborline Originates Residential Home loans in Florida and Commercial and business financing in all 50 States. We have over 25 years of experience in ALL types of real estate and commercial lending. We are strategically partnered to help you obtain ALL</div>
  <div class="abs btn" style="left:112px;top:1700px;width:126px;height:45px;font-size:15px">CONTACT</div>
</section>

<section>
  <div class="abs mark" style="top:1906px"></div>
  <div class="abs kicker" style="top:1956px">AVAILABLE PROPERTIES</div>
  <div class="abs title" style="top:1987px">OUR EXCLUSIVE PROPERTIES</div>

  <div class="abs prop" style="left:9px;width:263px;background:linear-gradient(135deg,#e5e5e3,#8c8d8e 55%,#2d2d2d)" role="img" aria-label="White modern building facade"><span class="prop-label">12 Sunset Street</span></div>
  <div class="abs prop" style="left:623px;width:273px;background:linear-gradient(135deg,#6d87b4,#cfd1d3 50%,#2a2c31)" role="img" aria-label="Perforated panel apartment building"><span class="prop-label">56 Washington Street</span></div>
  <div class="abs prop" style="left:896px;width:292px;background:linear-gradient(135deg,#9a5a48,#2c3138 55%,#4e6a9a)" role="img" aria-label="Red cladding building with dark glass"><span class="prop-label">78 Oak Boulevard</span></div>
  <div class="abs prop-bar"></div>
  <div class="abs prop-active" role="img" aria-label="Featured building under a green overlay">
    <div class="abs" style="left:26px;top:311px;color:#fff;font-size:13px">2025 &nbsp; United states</div>
    <div class="abs" style="left:26px;top:329px;color:#fff;font-size:22px;font-weight:500">34 Union Avenue</div>
    <div class="abs" style="left:26px;top:362px;color:#fff;font-size:17px">Mortgage Interest Rates <span style="font-size:20px">38 %</span></div>
  </div>
</section>

<section>
  <div class="abs mark" style="top:2574px"></div>
  <div class="abs kicker" style="top:2623px">WE OFFER ALL MORTGAGE LENDING PRODUCTS.</div>
  <div class="abs title" style="top:2654px">MORTGAGE LENDING PRODUCTS</div>

  <div class="abs gauge-tag" style="left:112px;top:2727px">5.5 %</div>
  <div class="abs gauge-tag" style="left:112px;top:3056px">5.5 %</div>
  <svg class="abs" style="left:120px;top:2752px" width="40" height="302" viewBox="0 0 40 302">
    <rect x="3" y="0" width="6" height="302" fill="#b8b8b8"/>
    <g stroke="#1f3b1c" stroke-width="2">
      <path d="M9 10h18M9 30h12M9 50h18M9 70h12M9 90h18M9 110h12M9 130h18M9 150h12M9 170h18M9 190h12M9 210h18M9 230h12M9 250h18M9 270h12M9 290h18"/>
    </g>
  </svg>
  <svg class="abs" style="left:148px;top:2866px;z-index:2" width="60" height="16"><circle cx="8" cy="8" r="7" fill="#8cbb3c"/><text x="24" y="12" font-family="Montserrat,sans-serif" font-size="10" fill="#333">6.25 %</text></svg>
  <div class="abs" style="left:198px;top:2755px;width:400px;height:293px;background:linear-gradient(160deg,#e8f0fb,#c9dcf3 45%,#f2c24b 80%,#5f9a3c)" role="img" aria-label="Illustration of a house, rate document, pen and gold coins"></div>
  <div class="abs" style="left:178px;top:3066px;width:396px;text-align:center;font-size:24px;color:var(--green-dark);font-weight:500">Residential Home</div>

  <div class="abs calc">
    <div class="calc-head">CALCULATE YOUR MONTHLY PAYMENTS</div>
    <div class="calc-row" style="background:var(--row)"><span>Loan Amount</span><span>$ 150,000</span></div>
    <div class="calc-row" style="background:#fff"><span>Interest Rate</span><span>5.0 %</span></div>
    <div class="calc-row" style="background:var(--row)"><span>Term (Years)</span><span>30</span></div>
    <div class="calc-row calc-total"><span>Monthly Principal<br>and Interest</span><span>$805.23</span></div>
  </div>
</section>

<section>
  <div class="abs contact" role="img" aria-label="Dark green tinted photo of a house with garage"></div>
  <div class="abs contact-title">GET IN TOUCH</div>
  <div class="abs" style="left:452px;top:3253px;width:30px;height:30px;border-radius:50%;background:#fff"></div>

  <div class="abs info-icon" style="top:3326px"><svg width="18" height="22" viewBox="0 0 18 22"><path d="M9 1a7 7 0 0 0-7 7c0 5 7 13 7 13s7-8 7-13a7 7 0 0 0-7-7z" fill="#8cbb3c"/><circle cx="9" cy="8" r="2.6" fill="#fff"/></svg></div>
  <div class="abs info-label" style="top:3331px">LOCATION:</div>
  <div class="abs info-value" style="top:3364px">465 Lorum Ipsum Dolore, Western Australia</div>

  <div class="abs info-icon" style="top:3405px"><svg width="20" height="20" viewBox="0 0 20 20"><path d="M4 1l4 4-2 3c1 2 3 4 6 6l3-2 4 4-3 3C9 19 1 11 1 4z" fill="#8cbb3c"/></svg></div>
  <div class="abs info-label" style="top:3410px">PHONE:</div>
  <div class="abs info-value" style="top:3443px">08 (888) 888 8888</div>

  <div class="abs info-icon" style="top:3487px"><svg width="22" height="16" viewBox="0 0 22 16"><rect width="22" height="16" rx="2" fill="#8cbb3c"/><path d="M1 2l10 7 10-7" stroke="#fff" stroke-width="1.6" fill="none"/></svg></div>
  <div class="abs info-label" style="top:3492px">EMAIL:</div>
  <div class="abs info-value" style="top:3525px">info@harborlinelendingandcapital.example</div>

  <div class="abs field" style="top:3261px">Full Name</div>
  <div class="abs field" style="top:3321px">Phone Number</div>
  <div class="abs field" style="top:3382px">Email Address</div>
  <div class="abs field" style="top:3443px;height:87px">Your Message</div>
  <div class="abs btn" style="left:612px;top:3563px;width:174px;height:45px;font-size:16px">SEND MESSAGE</div>
</section>

<footer>
  <div class="abs" style="left:84px;top:3680px;display:flex;align-items:center;gap:22px">
    <span style="width:110px;height:110px;border-radius:50%;background:var(--green-dark);display:block"></span>
    <span class="brand-name">HARBORLINE LENDING AND CAPITAL OF FLORIDA<br>BUSINESS AND COMMERCIAL DIVISION</span>
  </div>
  <div class="abs foot-nav" style="left:798px">Home</div>
  <div class="abs foot-nav" style="left:901px">About</div>
  <div class="abs foot-nav" style="left:1004px">Properties</div>
  <div class="abs social" style="left:961px"></div>
  <div class="abs social" style="left:1014px"></div>
  <div class="abs social" style="left:1070px"></div>
  <div class="abs" style="left:925px;top:3774px;font-size:11.5px;color:#333">© 2025. All Rights Reserved.</div>
</footer>
</body>
</html>
```